Breakfast Cafe - The Sunny Nook

It is for my breakfast and lunch cafe with a hawaiian / beach theme. I am open 7 days a week from 7am to 2pm. We serve traditional American food such as omelettes, pancakes, burgers and sandwiches. I'll upload my old card and my new logo to be used. We have a lot of day to day regulars who eat there during the week, our t-shirts actually say 'Locals Only' on them. Hope this helps. Thanks.

Target Market(s)

anyone who has an appetite!

Industry/Entity Type

American Restaurant

Contact Information for Business Card

4815C Marlow Grove Avenue
Long Beach, California
(555) 731-2294

Requirements
Must have
• Address and phone number easily readable.
Nice to have
• beach or tropical theme

```html
<!DOCTYPE html>
<html lang="en">
<head>
<meta charset="utf-8">
<title>The Sunny Nook – Business Card</title>
<link href="https://fonts.googleapis.com/css2?family=Questrial&display=swap" rel="stylesheet">
<style>
  :root {
    --page: #f5f5f5;
    --sky: #42a9ee;
    --cloud: #62b5f0;
    --cloud-low: #7cc3f4;
    --sand: #f7e09a;
    --sea: #447fc0;
    --brand: #b8652a;
    --badge: #f2a648;
    --white: #ffffff;
  }
  * { margin: 0; padding: 0; box-sizing: border-box; }
  html, body {
    width: 1200px; height: 1198px; overflow: hidden;
    background: var(--page);
    font-family: "Questrial", "Century Gothic", sans-serif;
  }
  .card {
    position: absolute;
    top: 261px;
    width: 386px; height: 643px;
    overflow: hidden;
  }
  .card--front { left: 139px; }
  .card--back { left: 658px; }
  .card svg { display: block; width: 100%; height: 100%; }
  .brand-name { font-family: "Questrial", sans-serif; fill: var(--brand); font-weight: 400; }
  .brand-place { font-family: "Questrial", sans-serif; fill: var(--brand); letter-spacing: 4px; font-weight: 400; }
  .contact { font-family: "Questrial", sans-serif; fill: var(--white); }
  .hours { font-family: "Questrial", sans-serif; fill: var(--white); }
</style>
</head>
<body>

<!-- Front -->
<div class="card card--front">
  <svg viewBox="0 0 386 643" xmlns="http://www.w3.org/2000/svg">
    <rect class="sky" width="386" height="643" fill="var(--sky)"/>
    <path class="clouds" fill="var(--cloud)" d="M0 156 C30 146 50 150 64 152 C74 118 118 118 132 140 C150 126 172 130 180 144 C200 130 224 134 236 148 C256 134 290 136 304 152 C326 144 360 150 386 148 V643 H0 Z"/>
    <path class="clouds-low" fill="var(--cloud-low)" d="M0 336 C12 316 40 312 54 326 C70 306 104 312 110 330 C140 318 170 322 190 332 C220 320 262 318 290 330 C310 300 356 302 372 326 L386 322 V643 H0 Z"/>
    <path class="sand" fill="var(--sand)" d="M0 486 C80 496 150 502 230 488 C300 478 350 470 386 472 V643 H0 Z"/>

    <circle class="brand-badge" cx="193" cy="287" r="110" fill="var(--badge)" role="img" aria-label="Round badge area for the cafe emblem"/>
    <text class="brand-name" x="193" y="420" text-anchor="middle" font-size="40">The Sunny Nook</text>
    <text class="brand-place" x="193" y="451" text-anchor="middle" font-size="12">LONG BEACH, CA</text>
  </svg>
</div>

<!-- Back -->
<div class="card card--back">
  <svg viewBox="0 0 386 643" xmlns="http://www.w3.org/2000/svg">
    <rect class="sky" width="386" height="643" fill="var(--sky)"/>
    <path class="clouds" fill="var(--cloud)" d="M0 160 C30 150 56 154 66 158 C80 128 120 130 130 150 C170 140 210 146 240 152 C260 140 300 142 316 156 C340 148 366 152 386 150 V643 H0 Z"/>
    <path class="clouds-low" fill="var(--cloud-low)" d="M0 340 C14 318 44 316 56 330 C74 312 104 316 112 332 C150 320 200 326 230 330 C246 306 286 306 300 322 C330 310 366 316 386 340 V643 H0 Z"/>
    <path class="sea" fill="var(--sea)" d="M0 520 C60 505 120 500 170 505 C220 512 250 492 300 506 C340 518 366 520 386 516 V643 H0 Z"/>
    <path class="sand" fill="var(--sand)" d="M0 492 C90 492 170 520 240 570 C270 592 300 620 360 643 H0 Z"/>

    <circle class="brand-badge" cx="193" cy="158" r="95" fill="var(--badge)" role="img" aria-label="Round badge area for the cafe emblem"/>
    <text class="brand-name" x="193" y="264" text-anchor="middle" font-size="34">The Sunny Nook</text>
    <text class="brand-place" x="193" y="289" text-anchor="middle" font-size="11">LONG BEACH, CA</text>

    <g class="icon-pin" transform="translate(62 346)">
      <circle r="12" fill="var(--white)"/>
      <path d="M0 -7 C-4 -7 -6 -4 -6 -1 C-6 3 0 8 0 8 C0 8 6 3 6 -1 C6 -4 4 -7 0 -7 Z" fill="var(--cloud-low)"/>
      <circle cy="-1.5" r="2.2" fill="var(--white)"/>
    </g>
    <text class="contact" x="85" y="351" font-size="17">4815C Marlow Grove Avenue</text>
    <text class="contact" x="85" y="374" font-size="17">Long Beach, California</text>

    <g class="icon-phone" transform="translate(62 401)">
      <circle r="12" fill="var(--white)"/>
      <path d="M-5 -6 L-2 -6 L-1 -2 L-3 0 C-2 2 0 4 2 5 L4 3 L7 4 L7 7 C7 8 6 8 5 8 C-3 7 -8 1 -8 -4 C-8 -5 -7 -6 -5 -6 Z" fill="var(--cloud-low)"/>
    </g>
    <text class="contact" x="85" y="407" font-size="17">(555) 731-2294</text>

    <text class="hours" x="73" y="455" font-size="20" letter-spacing="0.5">BREAKFAST AND LUNCH</text>
    <text class="hours" x="73" y="484" font-size="20">7am-2pm daily</text>
  </svg>
</div>

</body>
</html>
```